Cosmetic oil label design

We need a label for a cosmetic oganic Argan Oil. The oil is organic imported from Morocco, cold pressed without any preservatives. The lable is for our round 30ml Airless Bottle with clear body Matte Gold Cap, Shiny Gold Collar. We want to communicate that our product is organic natural and works for all beauty needs. We want the emphasis on the words No preservatives, additives or perfumes
We have attached a picture of the bottle and our compnay's logo.

the bottle demensions are Width/Front: 33.0mm
Length/Depth: 33.0mm
Height: 115.0mm
Lable demensions: Lenght 4inch, width 1.75inch.

let us know if you need any other information, cheers!
Updates

Target Market(s)

Our target customer is mainly women 16-70, and also men or anyone looking to have healthy skin and hair using natural products

Industry/Entity Type

Product

Requirements
Must have
• Front side must have:
- attached logo
-words: Authentic Moroccan Argan Oil, No preservatives, additives or perfumes,
L’Huile d’Argan, Produit du Maroc, Imported from Morocco, 30ml

Back side
-Ingredients: 100% Pure Argania Spinosa (Argan Oil)
-Directions: Message into skin, hair or desired area until completely absorbed
-Manufactured for and distributed by Velora Traders
482 W 97th street New York , NY 10027
Nice to have
• Would be nice if we can fit the following information in the back of the label

Rich in vitamin E and essential fatty acids,Argan oil has several benefits. It Hydrates and nourishes skin and hair. Can be used for treating dry skin, split ends softening cuticles. It works for all types of skin.

```html
<!DOCTYPE html>
<html lang="en">
<head>
<meta charset="utf-8">
<title>Solena Moroccan Argan Oil – 30ml Label</title>
<link rel="stylesheet" href="https://fonts.googleapis.com/css2?family=Cinzel:wght@400;500&family=Questrial&family=Cormorant+Garamond:wght@500&display=swap">
<style>
  :root {
    --espresso: #221a15;
    --espresso-deep: #1e1712;
    --gold: #e9bb5c;
    --gold-soft: #efc566;
    --bronze: #8c6a3d;
    --umber: #3b2f25;
    --olive: #8d8434;
    --ink: #231a14;
  }
  html, body {
    margin: 0;
    padding: 0;
    width: 1200px;
    height: 2743px;
    overflow: hidden;
    background: var(--espresso);
  }
  .label {
    position: relative;
    width: 1200px;
    height: 2743px;
    overflow: hidden;
    background: var(--espresso);
  }
  .label__body {
    position: absolute;
    left: 0;
    top: 834px;
    width: 1200px;
    height: 1669px;
    background: linear-gradient(to bottom,
      var(--espresso) 0%,
      #6e5331 14%,
      #c8994c 28%,
      var(--gold) 38%,
      #d6a956 52%,
      var(--bronze) 72%,
      #5a4632 88%,
      var(--umber) 100%);
  }
  .label__cap {
    position: absolute;
    left: 0;
    top: 0;
    width: 1200px;
    height: 1060px;
  }
  .volume {
    position: absolute;
    top: 52px;
    right: 58px;
    margin: 0;
    font-family: "Cormorant Garamond", serif;
    font-weight: 500;
    font-size: 74px;
    color: var(--gold);
    line-height: 1;
  }
  .brand {
    position: absolute;
    left: 0;
    top: 640px;
    width: 1200px;
    display: flex;
    justify-content: center;
    align-items: center;
    gap: 34px;
  }
  .brand__name {
    font-family: "Cinzel", serif;
    font-weight: 400;
    font-size: 150px;
    color: var(--olive);
    letter-spacing: 6px;
    line-height: 1;
  }
  .brand__dot {
    width: 70px;
    height: 70px;
    border-radius: 50%;
    background: var(--olive);
  }
  .product-name {
    position: absolute;
    left: 0;
    top: 1355px;
    width: 1200px;
    margin: 0;
    text-align: center;
    font-family: "Cinzel", serif;
    font-weight: 400;
    font-size: 150px;
    line-height: 188px;
    color: var(--ink);
    letter-spacing: 2px;
  }
  .claim {
    position: absolute;
    left: 0;
    top: 2318px;
    width: 1200px;
    margin: 0;
    text-align: center;
    font-family: "Questrial", sans-serif;
    font-size: 70px;
    line-height: 80px;
    color: var(--gold);
  }
  .origin {
    position: absolute;
    left: 0;
    top: 2503px;
    width: 1200px;
    height: 240px;
    background: var(--espresso-deep);
  }
  .origin__text {
    margin: 0;
    padding-top: 46px;
    text-align: center;
    font-family: "Questrial", sans-serif;
    font-size: 60px;
    line-height: 76px;
    color: var(--gold-soft);
  }
</style>
</head>
<body>
  <main class="label">
    <div class="label__body"></div>

    <svg class="label__cap" viewBox="0 0 1200 1060" aria-hidden="true">
      <rect x="0" y="0" width="1200" height="834" fill="var(--espresso)"/>
      <ellipse cx="600" cy="834" rx="543" ry="206" fill="var(--espresso)"/>
    </svg>

    <p class="volume">30ml</p>

    <div class="brand">
      <span class="brand__name">Solena</span>
      <span class="brand__dot"></span>
    </div>

    <h1 class="product-name">Moroccan<br>Argan<br>Oil</h1>

    <p class="claim">No preservatives, additives<br>or parfumes</p>

    <footer class="origin">
      <p class="origin__text">L’Huile d’Argan, Produit du Maroc,<br>Imported from Morocco.</p>
    </footer>
  </main>
</body>
</html>
```